Coastline Premier Retreats Business Card Design

Design a business card for Coastline Premier Retreats. Look at the website for colors and reference. Card should have logo, name, title, office number, mobile number, email, URL and a tagline like, "Luxury Hotel & Resort Email Marketing" (This might change).

https://www.coastlinepremierretreats.example

The rest I will leave up to your imagination.

Contact Information for Business Card

Logo, name, title, office number, mobile number, email, URL and a tagline like, "Luxury Hotel & Resort Email Marketing" (This might change).

```html
<!DOCTYPE html>
<html lang="en">
<head>
<meta charset="utf-8">
<title>Coastline Premier Retreats – Business Card</title>
<link rel="stylesheet" href="https://fonts.googleapis.com/css2?family=Montserrat:wght@400;500;700;800&display=swap">
<style>
  :root {
    --stage: #2b2b2b;
    --card: #1d1d1d;
    --accent: #f07a12;
    --ink: #ffffff;
    --ink-soft: #e9e9e9;
  }
  * { box-sizing: border-box; margin: 0; padding: 0; }
  html, body { width: 1200px; height: 900px; overflow: hidden; }
  body {
    background: var(--stage);
    font-family: "Montserrat", Arial, sans-serif;
    display: flex;
    flex-direction: column;
    align-items: center;
    justify-content: center;
    gap: 44px;
  }
  .card {
    position: relative;
    width: 640px;
    height: 366px;
    background: var(--card);
    border-bottom: 4px solid var(--accent);
    border-left: 4px solid var(--accent);
    overflow: hidden;
  }

  /* Front */
  .card--front {
    display: flex;
    flex-direction: column;
    align-items: center;
    justify-content: center;
    gap: 34px;
  }
  .brand {
    display: flex;
    align-items: center;
    gap: 14px;
  }
  .brand__mark {
    width: 14px;
    height: 14px;
    background: var(--accent);
    flex: none;
  }
  .brand__name {
    color: var(--ink);
    font-weight: 800;
    text-transform: uppercase;
    line-height: 1.05;
    letter-spacing: 0.02em;
  }
  .card--front .brand__name { font-size: 38px; }
  .tagline {
    color: var(--accent);
    font-size: 17px;
    font-weight: 500;
    letter-spacing: 0.04em;
  }

  /* Back */
  .card--back .brand {
    position: absolute;
    top: 60px;
    left: 56px;
    gap: 10px;
  }
  .card--back .brand__mark { width: 9px; height: 9px; }
  .card--back .brand__name { font-size: 19px; }

  .person {
    position: absolute;
    top: 60px;
    right: 40px;
    text-align: right;
  }
  .person__name {
    color: var(--accent);
    font-size: 26px;
    font-weight: 800;
    letter-spacing: 0.04em;
    text-transform: uppercase;
  }
  .person__title {
    color: var(--ink-soft);
    font-size: 13px;
    margin-top: 2px;
  }
  .person__tab {
    position: absolute;
    top: 58px;
    right: 0;
    width: 22px;
    height: 36px;
    background: var(--accent);
  }

  .contact {
    position: absolute;
    left: 56px;
    bottom: 40px;
    color: var(--ink);
    font-size: 14px;
    line-height: 1.45;
  }
  .contact__address { margin-bottom: 14px; }
  .contact__list { list-style: none; }
  .contact__item {
    display: flex;
    align-items: center;
    gap: 10px;
  }
  .contact__icon {
    width: 12px;
    height: 12px;
    flex: none;
    fill: var(--accent);
  }
</style>
</head>
<body>

  <section class="card card--front" aria-label="Card front">
    <div class="brand">
      <span class="brand__mark"></span>
      <span class="brand__name">Coastline Premier<br>Retreats</span>
    </div>
    <p class="tagline">Luxury Hotel &amp; Resort Email Marketing</p>
  </section>

  <section class="card card--back" aria-label="Card back">
    <div class="brand">
      <span class="brand__mark"></span>
      <span class="brand__name">Coastline Premier<br>Retreats</span>
    </div>

    <span class="person__tab"></span>
    <div class="person">
      <p class="person__name">Daniel Marsh</p>
      <p class="person__title">CEO/Founder</p>
    </div>

    <div class="contact">
      <p class="contact__address">Po Box, 48 Harbor Lane<br>Bayview, CA 90210</p>
      <ul class="contact__list">
        <li class="contact__item">
          <svg class="contact__icon" viewBox="0 0 12 12" aria-hidden="true"><path d="M3 0h6a1 1 0 0 1 1 1v10a1 1 0 0 1-1 1H3a1 1 0 0 1-1-1V1a1 1 0 0 1 1-1zm0 1.5v8h6v-8zm3 8.7a.6.6 0 1 0 0 1.2.6.6 0 0 0 0-1.2z"/></svg>
          555.014.2200
        </li>
        <li class="contact__item">
          <svg class="contact__icon" viewBox="0 0 12 12" aria-hidden="true"><path d="M1 4c0-2 2-3 5-3s5 1 5 3v1H8V3.8C7.4 3.5 6.7 3.4 6 3.4s-1.4.1-2 .4V5H1zM3 6h6l2 5H1z"/></svg>
          +1 555 017 3849
        </li>
        <li class="contact__item">
          <svg class="contact__icon" viewBox="0 0 12 12" aria-hidden="true"><path d="M0 2h12v8H0zm1.2 1.2v.3L6 6.6l4.8-3.1v-.3zm0 1.7v3.9h9.6V4.9L6 8z"/></svg>
          info@coastlinepremierretreats.example
        </li>
        <li class="contact__item">
          <svg class="contact__icon" viewBox="0 0 12 12" aria-hidden="true"><path d="M6 0a6 6 0 1 1 0 12A6 6 0 0 1 6 0zm0 1.2a4.8 4.8 0 0 0-3.7 1.8l1.2 1 .3 1.5 1.4.9-.4 1.8L6 10.8a4.8 4.8 0 0 0 4.6-3.7L9 6.2 8 3.8l1-1.4A4.8 4.8 0 0 0 6 1.2z"/></svg>
          www.coastlinepremierretreats.example
        </li>
      </ul>
    </div>
  </section>

</body>
</html>
```